New Interrior Decoration company needs new website

We need a website for our new company specialising in interior decoration to residential and commercial markets.
We supply and install decorative and printed films for office and home decoration such as feature walls.
We would like to keep the design simple and clean.

Target Market(s)

Architects and interior designaers

Industry/Entity Type

It Company

Number of Pages Required

5+ page

Font styles to use
Sans Serif

Requirements
Must have
• Home page,
• Services/products page (split into commercial and residential)
• Gallery (split into commercial and residential)
• contact form and page
Nice to have
• Very clean and minimalistic design.

```html
<!DOCTYPE html>
<html lang="en">
<head>
<meta charset="utf-8">
<title>Lumen Interiors</title>
<link href="https://fonts.googleapis.com/css2?family=Lato:ital,wght@0,400;0,700;1,900&family=Arimo:wght@400;700&display=swap" rel="stylesheet">
<style>
:root{
  --blue:#0a5bb8;
  --blue-deep:#0b4f9e;
  --ink:#222;
  --muted:#7a7a7a;
  --pale:#eeeeee;
  --footer:#333333;
  --footer-base:#222222;
  --icon-grey:#9a9a9a;
  --white:#fff;
}
*{margin:0;padding:0;box-sizing:border-box}
html,body{width:1200px;height:2875px;overflow:hidden}
body{position:relative;background:var(--white);font-family:"Arimo",Arial,sans-serif;color:var(--ink)}
.abs{position:absolute}
.heading{font-family:"Lato",Arial,sans-serif;font-weight:400;text-transform:uppercase;color:var(--ink);text-align:center;width:100%}
.heading span{color:var(--blue)}
.btn{position:absolute;left:506px;width:188px;height:61px;background:var(--blue);color:var(--white);font-family:"Lato",Arial,sans-serif;font-size:21px;display:flex;align-items:center;justify-content:center;border-radius:4px;text-transform:uppercase}

/* header */
.site-header{top:0;left:0;width:1200px;height:110px}
.brand{left:77px;top:20px;display:flex;align-items:center;gap:12px}
.brand-mark{width:72px;height:72px;background:var(--blue)}
.brand-name{font-family:"Lato",Arial,sans-serif;font-weight:700;font-size:36px;line-height:34px;color:#2b2b2b;text-transform:uppercase}
.call{left:572px;top:38px;font-size:21px;color:var(--blue)}
.call b{color:var(--ink);font-size:27px;font-weight:700;margin-left:8px}
.follow{left:863px;top:40px;font-size:21px;color:var(--blue)}
.socials{display:flex;gap:12px}
.socials i{display:block;width:40px;height:40px;background:var(--icon-grey)}
.socials i:first-child{background:var(--blue)}
.socials-top{left:979px;top:36px}

.main-nav{top:110px;left:0;width:1200px;height:62px;background:var(--blue)}
.main-nav a{position:absolute;top:0;height:62px;line-height:62px;color:var(--white);font-size:17px;text-decoration:none;text-transform:uppercase;text-align:center}
.main-nav a.active{background:#000}

.hero{top:172px;left:0;width:1200px;height:522px;background:linear-gradient(160deg,#8d8b86 0%,#c9c7c2 35%,#6f6b66 70%,#4b4845 100%)}
.hero-title{top:382px;left:0;width:1200px;text-align:center;font-family:"Lato",Arial,sans-serif;font-style:italic;font-weight:900;font-size:41px;line-height:52px;color:var(--white);text-shadow:2px 2px 4px rgba(0,0,0,.7);text-transform:uppercase}

/* welcome */
.welcome-title{top:748px;font-size:43px}
.welcome-text{top:806px;left:140px;width:920px;text-align:center;font-size:15px;line-height:27px;color:var(--muted)}

/* services */
.service{top:1079px;width:600px;height:416px;color:var(--white);text-align:center}
.service-commercial{left:0;background:linear-gradient(135deg,#1b63c4,#0a4c9f)}
.service-residential{left:600px;background:linear-gradient(135deg,#3a3a3a,#1d1d1d)}
.service-photo{position:absolute;left:215px;top:64px;width:249px;height:164px;border:2px solid rgba(255,255,255,.85)}
.service-commercial .service-photo{background:linear-gradient(180deg,#d9d6cf,#8a7f70)}
.service-residential .service-photo{background:linear-gradient(180deg,#e4e9b8,#b8c46a)}
.service-title{position:absolute;top:250px;width:100%;font-family:"Lato",Arial,sans-serif;font-size:22px;text-transform:uppercase}
.service-text{position:absolute;top:288px;left:145px;width:310px;font-size:15px;line-height:25px}
.service-residential .service-text{color:#aaa}

/* gallery */
.gallery{top:1495px;left:0;width:1200px;height:713px;background:var(--pale)}
.gallery-title{top:58px;font-size:43px}
.tile{position:absolute;width:333px;height:208px}
.tile-feature{background:var(--blue);border:2px solid #3d7fd0;color:var(--white);text-align:center;padding-top:84px}
.tile-feature strong{display:block;font-size:23px;font-weight:700;text-transform:uppercase}
.tile-feature small{display:block;font-size:17px;margin-top:6px}

/* testimonial */
.testimonial-title{top:2268px;font-size:41px}
.quote-mark{top:2345px;left:576px}
.testimonial-text{top:2404px;left:190px;width:820px;text-align:center;font-size:15px;line-height:26px;color:var(--muted)}
.testimonial-name{top:2493px;left:0;width:1200px;text-align:center;font-size:16px;font-weight:700;color:var(--blue);text-transform:uppercase}
.arrow{top:2398px}

/* footer */
.site-footer{top:2575px;left:0;width:1200px;height:237px;background:var(--footer);color:#c8c8c8;font-size:14px}
.footer-col{position:absolute;top:30px}
.footer-col h4{font-size:16px;font-weight:700;color:var(--blue);text-transform:uppercase;margin-bottom:22px}
.link-list{list-style:none}
.link-list li{line-height:27px;padding-left:22px;position:relative}
.link-list li::before{content:"";position:absolute;left:2px;top:11px;width:7px;height:7px;border-radius:50%;background:var(--blue)}
.contact-row{display:flex;gap:14px;margin-bottom:16px;line-height:21px}
.contact-row svg{flex:none}
.email-field{width:250px;height:46px;border:1px solid #777;margin-top:12px;padding-left:14px;line-height:44px;color:#777;font-size:13px}
.subscribe{width:250px;height:46px;background:var(--blue);color:var(--white);margin-top:10px;text-align:center;line-height:46px;font-family:"Lato",Arial,sans-serif;font-size:18px;text-transform:uppercase}
.footer-brand{left:872px;top:30px;display:flex;align-items:center;gap:10px}
.footer-brand .brand-mark{width:44px;height:44px}
.footer-brand .brand-name{color:var(--blue);font-size:25px;line-height:24px}
.footer-rule{left:872px;top:90px;width:252px;height:1px;background:#555}
.socials-footer{left:928px;top:115px}
.base-bar{top:2812px;left:0;width:1200px;height:63px;background:var(--footer-base);color:#ddd;font-size:14px;text-align:center;line-height:63px}
.base-bar span{color:var(--blue)}
</style>
</head>
<body>

<header class="site-header abs">
  <div class="brand abs"><div class="brand-mark"></div><div class="brand-name">Lumen<br>Interiors</div></div>
  <div class="call abs">Call Us <b>: 020 555 0147</b></div>
  <div class="follow abs">Follow Us :</div>
  <div class="socials socials-top abs" aria-label="Social links"><i></i><i></i><i></i></div>
</header>

<nav class="main-nav abs">
  <a class="active" style="left:264px;width:112px">Home</a>
  <a style="left:406px;width:112px">About Us</a>
  <a style="left:553px;width:112px">Services</a>
  <a style="left:697px;width:112px">Gallery</a>
  <a style="left:839px;width:112px">Contact</a>
</nav>

<section class="hero abs" role="img" aria-label="Photo of a modern open kitchen and dining area with white table, black chairs and pendant lamps">
</section>
<h1 class="hero-title abs">We are specialising in interior decoration for<br>residential &amp; commercial markets.</h1>

<section>
  <h2 class="heading welcome-title abs">Welcome to <span>Lumen Interiors</span></h2>
  <p class="welcome-text abs">Lorem Ipsum is simply dummy text of the printing and typesetting industry. Lorem Ipsum has been the industry's standard dummy text ever since the 1500s, when an unknown printer took a galley of type and scrambled it to make Lorem Ipsum is simply dummy text of the printing and typesetting industry. Lorem Ipsum has been the industry's standard dummy text ever since the 1500s, when an unknown printer took a galley of type and scrambled it to make a type specimen book. It has survived not only five centuries, but also the leap into electronic</p>
  <a class="btn" style="top:955px">Know More</a>
</section>

<section class="service service-commercial abs" role="img" aria-label="Commercial interior photo under a blue tint">
  <div class="service-photo" role="img" aria-label="Photo of a commercial office interior"></div>
  <h3 class="service-title">Commercial Design</h3>
  <p class="service-text">Lorem Ipsum is simply dummy text of the printing and typesetting industry. Lorem Ipsum has been the industry's standard..</p>
</section>
<section class="service service-residential abs" role="img" aria-label="Residential living room photo under a dark tint">
  <div class="service-photo" role="img" aria-label="Photo of a bright residential living room"></div>
  <h3 class="service-title">Residential Design</h3>
  <p class="service-text">Lorem Ipsum is simply dummy text of the printing and typesetting industry. Lorem Ipsum has been the industry's standard..</p>
</section>

<section class="gallery abs">
  <h2 class="heading gallery-title abs">Our <span>Gallery</span></h2>
  <div class="tile tile-feature" style="left:77px;top:132px"><strong>Dream House</strong><small>Residential</small></div>
  <div class="tile" style="left:433px;top:132px;background:linear-gradient(135deg,#5a2a18,#2a1a14)" role="img" aria-label="Photo of a white lounge chair against a dark red wall"></div>
  <div class="tile" style="left:790px;top:132px;background:linear-gradient(135deg,#e8e6e2,#b9b6b0)" role="img" aria-label="Photo of an office wall with printed circle graphics"></div>
  <div class="tile" style="left:77px;top:361px;background:linear-gradient(180deg,#8a4f58,#d8cfc6)" role="img" aria-label="Photo of a white sofa in a living room with a mauve wall"></div>
  <div class="tile" style="left:433px;top:361px;background:linear-gradient(180deg,#dcdcda,#6e7276)" role="img" aria-label="Photo of a grey kitchen with pendant lamps"></div>
  <div class="tile" style="left:790px;top:361px;background:linear-gradient(135deg,#c9a86a,#8fa06a,#d0452e)" role="img" aria-label="Photo of a wood-panel feature wall with red chairs"></div>
  <a class="btn" style="top:591px">View All</a>
</section>

<section>
  <h2 class="heading testimonial-title abs">What our <span>client say</span></h2>
  <svg class="quote-mark abs" width="40" height="32" viewBox="0 0 40 32" aria-hidden="true"><path fill="#0a5bb8" d="M0 32V18C0 8 5 2 15 0l2 4C11 6 9 10 9 14h8v18zM22 32V18c0-10 5-16 15-18l2 4c-6 2-8 6-8 10h8v18z"/></svg>
  <p class="testimonial-text abs">Lorem Ipsum is simply dummy text of the printing and typesetting industry. Lorem Ipsum has been the industry's standard dummy text ever since the 1500s, when an unknown printer took a galley of type and scrambled it to make a type specimen book. It has survived not only five centuries,</p>
  <p class="testimonial-name abs">- Maren Holt</p>
  <svg class="arrow abs" style="left:120px" width="60" height="60" viewBox="0 0 60 60" aria-label="Previous"><circle cx="30" cy="30" r="28" fill="#fff" stroke="#555" stroke-width="2"/><path d="M34 19 23 30l11 11" fill="none" stroke="#333" stroke-width="4"/></svg>
  <svg class="arrow abs" style="left:1019px" width="60" height="60" viewBox="0 0 60 60" aria-label="Next"><circle cx="30" cy="30" r="28" fill="#fff" stroke="#555" stroke-width="2"/><path d="M26 19 37 30 26 41" fill="none" stroke="#333" stroke-width="4"/></svg>
</section>

<footer class="site-footer abs">
  <div class="footer-col" style="left:77px">
    <h4>Usefull Links</h4>
    <ul class="link-list"><li>Home</li><li>About Us</li><li>Services</li><li>Gallery</li><li>Contact</li></ul>
  </div>
  <div class="footer-col" style="left:311px;width:270px">
    <h4>Get In Touch</h4>
    <div class="contact-row"><svg width="22" height="26" viewBox="0 0 22 26" aria-hidden="true"><path fill="#0a5bb8" d="M10 0h2v26h-2zM2 4h16l4 3-4 3H2zM4 13h16v6H4l-4-3z"/></svg><span>Lorem Ipsum is simple dummy text of printing and type srettin</span></div>
    <div class="contact-row"><svg width="22" height="18" viewBox="0 0 22 18" aria-hidden="true"><rect width="22" height="16" y="1" fill="#0a5bb8"/><path d="M1 2l10 8 10-8" fill="none" stroke="#333" stroke-width="2"/></svg><span>info@lumeninteriors.com</span></div>
    <div class="contact-row"><svg width="22" height="22" viewBox="0 0 22 22" aria-hidden="true"><path fill="#0a5bb8" d="M5 1l4 5-2 3c1 3 3 5 6 6l3-2 5 4-3 4C9 21 1 13 1 4z"/></svg><span>020 555 0182</span></div>
  </div>
  <div class="footer-col" style="left:598px">
    <h4>Newsletter</h4>
    <div>Subscribe to the newsletter</div>
    <div class="email-field">Enter Your Email *</div>
    <div class="subscribe">Subscribr</div>
  </div>
  <div class="footer-brand abs"><div class="brand-mark"></div><div class="brand-name">Lumen<br>Interiors</div></div>
  <div class="footer-rule abs"></div>
  <div class="socials socials-footer abs" aria-label="Social links"><i></i><i></i><i></i></div>
</footer>
<div class="base-bar abs">&copy;<span>LumenInteriors</span> - 2016. All rights reserved.</div>

</body>
</html>
```